Larkspur Talent IT Recruiting firm needs a business card design for Recruiters, Sourcers, and Account

We need business cards that allow us to change all contact info, names, titles (Recruiter, Sourcer, Account Manager, Director, CEO, etc) per person since we have three offices, in three cities, Phoenix, Austin, and Las Vegas. We do recruiting and contractors for IT positions (Developers, Architects, Software Engineers, Security Engineers, Help Desk, DBAs, PMs, Scrum Masters, etc.) Our client companies are very diverse from Meridian 100 to silicone Valley type start-ups.

So, while we what hip, techie, and quirky, it still needs to be professional. Primary color we use is blue, with silver as a secondary color.

Target Market(s)

IT, Technology

Industry/Entity Type

Business

Contact Information for Business Card

Company name: Larkspur Talent, Inc.
Website: www.larkspurtalent.example
Logos for Careerloop, Blipster, and Myriada

Name, Title, Office Number, Cell Number, email

Font styles to use
Serif
Sans Serif

Colors
0455a3
d5d5d5

Requirements
Nice to have
• The grey I selected below is not necessary - but, would like silver included. I included a card design (File 3: LTI early trial example.jpg) that I had started on. It's very rough, and not quite what we're looking for, but what we did like is the logo, big, maybe a bit faded, off center, goes out of frame, etc. Still looking for other ideas - you are the pros! But, just an idea of a design element we liked.

```html
<!DOCTYPE html>
<html lang="en">
<head>
<meta charset="utf-8">
<title>Larkspur Talent – Business Card</title>
<link rel="stylesheet" href="https://fonts.googleapis.com/css2?family=Cinzel:wght@400;500&family=Open+Sans:wght@400;600;700&display=swap">
<style>
  :root {
    --brand-blue: #0455a3;
    --brand-blue-light: #1f8fd6;
    --silver: #d5d5d5;
    --ink: #1c1c1c;
    --paper: #ffffff;
    --backdrop: #5a5a5a;
  }
  * { box-sizing: border-box; margin: 0; padding: 0; }
  html, body { width: 1200px; height: 904px; overflow: hidden; }
  body { background: var(--backdrop); position: relative; font-family: "Open Sans", Arial, sans-serif; }

  .card {
    position: absolute;
    width: 600px;
    height: 340px;
    border-radius: 34px;
    overflow: hidden;
  }

  /* Back of card */
  .card-back { left: 550px; top: 56px; background: var(--brand-blue); color: var(--paper); }
  .back-mark {
    position: absolute; left: 0; right: 0; top: 86px;
    display: flex; align-items: center; justify-content: center; gap: 18px;
  }
  .back-mark-dot { width: 64px; height: 64px; border-radius: 50%; background: var(--paper); }
  .back-mark-name { font-family: "Cinzel", Georgia, serif; font-weight: 400; font-size: 44px; letter-spacing: 2px; }
  .back-url {
    position: absolute; left: 0; right: 0; bottom: 46px; text-align: center;
    font-size: 20px; letter-spacing: 3px;
  }

  /* Front of card */
  .card-front { left: 50px; top: 476px; background: var(--paper); color: var(--ink); }
  .front-wave { position: absolute; inset: 0; }
  .brand-block { position: absolute; left: 40px; top: 30px; }
  .brand-name {
    font-family: "Cinzel", Georgia, serif; font-weight: 400; font-size: 40px;
    color: var(--ink); letter-spacing: 1px; line-height: 1;
  }
  .brand-tagline {
    margin-top: 10px; font-family: "Cinzel", Georgia, serif; font-size: 15px;
    letter-spacing: 3px; color: var(--ink);
  }
  .person { position: absolute; left: 40px; top: 130px; font-size: 15px; }
  .person-name { color: var(--brand-blue); font-weight: 700; font-size: 18px; }
  .contact-list { position: absolute; left: 44px; top: 172px; list-style: none; font-size: 15px; line-height: 23px; }
  .contact-list li { display: flex; align-items: center; gap: 8px; }
  .contact-icon { width: 13px; height: 13px; fill: none; stroke: var(--brand-blue); stroke-width: 1.6; }
  .social-list {
    position: absolute; right: 40px; top: 272px; list-style: none;
    color: var(--paper); font-size: 15px; line-height: 27px;
  }
  .social-list li { display: flex; align-items: center; gap: 9px; }
  .social-dot { width: 16px; height: 16px; border-radius: 50%; background: var(--paper); }
</style>
</head>
<body>

<section class="card card-back" aria-label="Business card back">
  <div class="back-mark">
    <span class="back-mark-dot"></span>
    <span class="back-mark-name">Larkspur Talent</span>
  </div>
  <p class="back-url">www.larkspurtalent.example</p>
</section>

<section class="card card-front" aria-label="Business card front">
  <svg class="front-wave" viewBox="0 0 600 340" preserveAspectRatio="none" aria-hidden="true">
    <path d="M0,212 C130,318 360,236 600,262 L600,340 L0,340 Z" fill="var(--brand-blue)"/>
    <path d="M0,236 C150,326 380,246 600,270" fill="none" stroke="var(--paper)" stroke-width="7"/>
  </svg>

  <div class="brand-block">
    <p class="brand-name">Larkspur Talent</p>
    <p class="brand-tagline">RISING TO THE CHALLENGE</p>
  </div>

  <p class="person"><span class="person-name">Dana Whitfield,</span> First Touch Embassador</p>

  <ul class="contact-list">
    <li>
      <svg class="contact-icon" viewBox="0 0 14 14"><path d="M3 1.5 L5 1.5 L6 4.5 L4.5 5.5 C5.3 7.3 6.7 8.7 8.5 9.5 L9.5 8 L12.5 9 L12.5 11 C12.5 12 11.5 12.7 10.5 12.5 C6 11.7 2.3 8 1.5 3.5 C1.3 2.5 2 1.5 3 1.5 Z"/></svg>
      512-555-0147
    </li>
    <li>
      <svg class="contact-icon" viewBox="0 0 14 14"><rect x="1" y="3" width="12" height="8" rx="1"/><path d="M1 3 L7 8 L13 3"/></svg>
      dana@larkspurtalent.example
    </li>
    <li>
      <svg class="contact-icon" viewBox="0 0 14 14"><circle cx="7" cy="7" r="5.8"/><ellipse cx="7" cy="7" rx="2.6" ry="5.8"/><path d="M1.2 7 H12.8"/></svg>
      www.larkspurtalent.example
    </li>
  </ul>

  <ul class="social-list">
    <li><span class="social-dot"></span>@DanaWhitfieldLT</li>
    <li><span class="social-dot"></span>@DanaWhitfieldLT</li>
  </ul>
</section>

</body>
</html>
```